real esate business card with company logo and name

we need a business card design for a real esate company

The company name is Walsh & Brand Pty Ltd, and we have our logo designed and will upload. We want classic or moden feel. Black or white background. looks more textured. Should include folowinginformations
Owen Walsh and Lucy Brand
Sales Agents & Onsite Manager
p: 07 5948 2063
F: 07 5948 2174
M:0431 857 219
3/42 Marlow Crescent, FERNLEA QLD 4213

We want this business card looks professonal. Thank you in advance.

Industry/Entity Type

Real Estate Agent

Contact Information for Business Card

Owen Walsh and Lucy Brand
Onsite Manager & Sales Agents
p: 07 5948 2063
M:0431 857 219

Font styles to use
Serif

Colors
000000
fbfbfb
333333
959595

Requirements
Must have
• company logo and name, black or white back ground

```html
<!DOCTYPE html>
<html lang="en">
<head>
<meta charset="utf-8">
<title>Walsh &amp; Brand Pty Ltd – Business Card</title>
<link rel="stylesheet" href="https://fonts.googleapis.com/css2?family=Roboto+Condensed:wght@400&family=Source+Sans+3:wght@400&display=swap">
<style>
  :root {
    --backdrop: #a3a0a1;
    --backdrop-light: #b0adae;
    --card: #fbfbfb;
    --card-edge: #55555a;
    --ink: #333333;
    --ink-soft: #5a5a5c;
    --mark: #959595;
  }
  * { box-sizing: border-box; margin: 0; padding: 0; }
  html, body { width: 1200px; height: 1200px; overflow: hidden; }
  body {
    background: radial-gradient(ellipse at 50% 30%, var(--backdrop-light), var(--backdrop) 70%);
    position: relative;
    font-family: "Source Sans 3", "Source Sans Pro", sans-serif;
  }

  .card-stack {
    position: absolute;
    width: 712px;
    height: 418px;
  }
  .card-stack--front { left: 238px; top: 120px; }
  .card-stack--back  { left: 230px; top: 645px; }

  .card-stack__edge {
    position: absolute;
    left: 10px; right: 4px; top: 8px; bottom: 0;
    background: var(--card-edge);
    border-radius: 26px;
    box-shadow: 0 18px 40px rgba(0,0,0,0.28), 0 4px 10px rgba(0,0,0,0.2);
  }

  .card {
    position: absolute;
    left: 0; top: 0;
    width: 712px;
    height: 410px;
    background: var(--card);
    border-radius: 26px;
    overflow: hidden;
  }
  .card__texture {
    position: absolute;
    inset: 0;
    width: 100%;
    height: 100%;
    opacity: 0.55;
  }

  .brand-mark {
    position: absolute;
    width: 78px;
    height: 78px;
    background: var(--mark);
  }
  .brand-name {
    position: absolute;
    font-family: "Roboto Condensed", sans-serif;
    font-weight: 400;
    color: var(--mark);
    letter-spacing: 0.5px;
    white-space: nowrap;
    transform: translateX(-50%);
  }
  .card--front .brand-mark { left: 315px; top: 145px; }
  .card--front .brand-name { left: 356px; top: 290px; font-size: 23px; }
  .card--back .brand-mark { left: 153px; top: 152px; }
  .card--back .brand-name { left: 192px; top: 281px; font-size: 23px; }

  .contact { position: absolute; left: 374px; top: 86px; color: var(--ink); }
  .contact__names { font-family: "Roboto Condensed", sans-serif; font-weight: 400; font-size: 27px; color: #3c3c3e; }
  .contact__role { font-family: "Roboto Condensed", sans-serif; font-size: 15px; color: var(--ink-soft); margin-top: 12px; }
  .contact__lines { list-style: none; margin-top: 44px; }
  .contact__lines li { display: flex; align-items: center; height: 26px; font-size: 17px; color: var(--ink-soft); }
  .contact__lines svg { width: 16px; height: 16px; margin-right: 19px; fill: var(--ink-soft); }
  .contact__address { font-size: 17px; line-height: 27px; color: var(--ink-soft); margin-top: 5px; }
</style>
</head>
<body>
  <svg width="0" height="0" style="position:absolute" aria-hidden="true">
    <filter id="paper-grain" x="0" y="0" width="100%" height="100%">
      <feTurbulence type="fractalNoise" baseFrequency="0.9" numOctaves="3" seed="4" result="noise"/>
      <feColorMatrix in="noise" type="matrix" values="0 0 0 0 0.55  0 0 0 0 0.55  0 0 0 0 0.56  0 0 0 0.22 0"/>
    </filter>
  </svg>

  <div class="card-stack card-stack--front">
    <div class="card-stack__edge"></div>
    <section class="card card--front">
      <svg class="card__texture" aria-hidden="true"><rect width="100%" height="100%" filter="url(#paper-grain)"/></svg>
      <div class="brand-mark"></div>
      <p class="brand-name">WALSH &amp; BRAND PTY LTD.</p>
    </section>
  </div>

  <div class="card-stack card-stack--back">
    <div class="card-stack__edge"></div>
    <section class="card card--back">
      <svg class="card__texture" aria-hidden="true"><rect width="100%" height="100%" filter="url(#paper-grain)"/></svg>
      <div class="brand-mark"></div>
      <p class="brand-name">WALSH &amp; BRAND PTY LTD.</p>

      <div class="contact">
        <h1 class="contact__names">Owen Walsh &amp; Lucy Brand</h1>
        <p class="contact__role">Sales Agents &amp; Onsite Manager</p>
        <ul class="contact__lines">
          <li>
            <svg viewBox="0 0 16 16" aria-hidden="true"><path d="M4 0h8a1.5 1.5 0 0 1 1.5 1.5v13A1.5 1.5 0 0 1 12 16H4a1.5 1.5 0 0 1-1.5-1.5v-13A1.5 1.5 0 0 1 4 0zm0 2v10h8V2zm4 11a1 1 0 1 0 0 2 1 1 0 0 0 0-2z"/></svg>
            0431 857 219
          </li>
          <li>
            <svg viewBox="0 0 16 16" aria-hidden="true"><path d="M1 5c0-2 3-3 7-3s7 1 7 3v1.5h-3.5V5h-7v1.5H1zM4 7.5h8l2 6.5H2zm4 1.5a2 2 0 1 0 0 4 2 2 0 0 0 0-4z"/></svg>
            07 5948 2063
          </li>
          <li>
            <svg viewBox="0 0 16 16" aria-hidden="true"><path d="M4 1h8v4H4zM1 6h14v6h-3v3H4v-3H1zm4 4v4h6v-4z"/></svg>
            07 5948 2174
          </li>
        </ul>
        <p class="contact__address">3/42 Marlow Crescent,<br>FERNLEA QLD 4213</p>
      </div>
    </section>
  </div>
</body>
</html>
```